Mark Tolvane actor business cards

I need unique and interesting business cards that have my headshot photo, my name, tagline/position/skills, contact info, preferred pronouns (he, him, his), and social media handles. These need to be memorable networking tools to hand out at events that stand out. I am an actor that works in theatre, film, and TV and usually play darker dramatic roles, though it doesn't have to necessarily need to be reflected in the design, but I am not a light, comedic actor. In my email tagline, My position/skills are "Actor, storyteller, theatre maker."

Target Market(s)

Casting directors, film and television community, theatre community.

Industry/Entity Type

Performing Art

Contact Information for Business Card

Mark Tolvane. Pronouns: he, him, his. Contact info: (555)-318-7064, Marktolvane.example, marktolvane@postbox.example. Talent representation: Kirwood Talent Agency. Social Media: Facebook page, twitter and instagram: @MarkTolvanePlays. Company Member of Harbin Theatre Company.

Font styles to use
Serif
Decorative

Colors

Designer to choose colors to be used in the design.

Requirements
Must have
• Headshot photo, name, tagline, preferred pronouns, contact info, Social media handle, talent agency logo, harbin theatre company logo. Both logos should be smaller than my name. Under or near Harbin logo, it should say "Company Member"
Nice to have
• I would like to have the photo, my name, tagline, and maybe pronouns on one side, and all contact info, and social media, and talent agency logo on the other. I would like the style to reflect my type which is a little more serious and somewhat darker, and definitely not comedic.
Should not have
• No extraneous theatre lights, camera, or film, etc. clip art or photos. Use solid backgrounds or photos provided.

```html
<!DOCTYPE html>
<html lang="en">
<head>
<meta charset="utf-8">
<title>Mark Tolvane — Business Cards</title>
<link rel="stylesheet" href="https://fonts.googleapis.com/css2?family=Cormorant+Garamond:ital,wght@1,600&family=Lato:wght@400;700&display=swap">
<style>
  :root {
    --backdrop: #2b2b2d;
    --card-dark: #0c0c0e;
    --card-light: #f3f3f4;
    --band: #0b0b18;
    --accent: #1fa3e3;
    --text-light: #e6e6e6;
    --text-dark: #161616;
    --photo-top: #3a3f4a;
    --photo-bottom: #5a74a8;
  }
  * { margin: 0; padding: 0; box-sizing: border-box; }
  html, body { width: 1200px; height: 900px; overflow: hidden; }
  body {
    background: var(--backdrop);
    font-family: "Lato", Arial, sans-serif;
    position: relative;
  }
  .card {
    position: absolute;
    top: 300px;
    width: 520px;
    height: 300px;
    border-radius: 22px;
    overflow: hidden;
  }
  /* Front */
  .card-front { left: 50px; background: var(--card-dark); color: var(--text-light); }
  .headshot {
    position: absolute;
    right: 0; top: 0;
    width: 245px; height: 300px;
    border-radius: 0 22px 22px 0;
    background: linear-gradient(180deg, var(--photo-top) 0%, #4a5a7c 55%, var(--photo-bottom) 100%);
  }
  .identity { position: absolute; left: 34px; top: 118px; }
  .name {
    font-family: "Cormorant Garamond", Georgia, serif;
    font-style: italic; font-weight: 600;
    font-size: 31px; color: var(--accent); line-height: 1;
  }
  .tagline { font-size: 13px; margin-top: 6px; }
  .contact-list { list-style: none; margin-top: 14px; font-size: 13px; }
  .contact-list li { display: flex; align-items: center; gap: 7px; margin-bottom: 4px; }
  .contact-list svg { width: 12px; height: 12px; fill: var(--accent); flex: none; }
  .social { position: absolute; left: 34px; top: 262px; display: flex; align-items: center; gap: 8px; font-size: 14px; }
  .social-dot { width: 20px; height: 20px; border-radius: 50%; background: var(--accent); }
  /* Back */
  .card-back { left: 630px; background: var(--card-light); }
  .agency { position: absolute; left: 140px; top: 68px; display: flex; align-items: center; gap: 12px; color: var(--text-dark); }
  .agency-dot { width: 34px; height: 34px; border-radius: 50%; background: var(--accent); }
  .agency-name { font-size: 34px; font-weight: 400; line-height: 1; }
  .agency-sub { font-size: 13px; margin-top: 4px; }
  .pronoun-band {
    position: absolute; left: 0; right: 0; top: 178px; height: 70px;
    background: var(--band);
    display: flex; align-items: flex-start; justify-content: center;
    padding-top: 14px;
  }
  .pronouns {
    font-family: "Cormorant Garamond", Georgia, serif;
    font-style: italic; font-weight: 600; font-size: 27px;
    color: var(--accent); letter-spacing: 1px;
  }
</style>
</head>
<body>
  <section class="card card-front">
    <div class="headshot" role="img" aria-label="Headshot photo of Mark Tolvane"></div>
    <div class="identity">
      <h1 class="name">Mark Tolvane</h1>
      <p class="tagline">Actor, Storyteller, Theatre Maker</p>
      <ul class="contact-list">
        <li><svg viewBox="0 0 24 24"><path d="M6.6 10.8a15 15 0 0 0 6.6 6.6l2.2-2.2a1 1 0 0 1 1-.25 11.4 11.4 0 0 0 3.6.6 1 1 0 0 1 1 1V20a1 1 0 0 1-1 1A17 17 0 0 1 3 4a1 1 0 0 1 1-1h3.5a1 1 0 0 1 1 1c0 1.25.2 2.45.6 3.6a1 1 0 0 1-.25 1z"/></svg>(555)-318-7064</li>
        <li><svg viewBox="0 0 24 24"><path d="M2 5h20v14H2z M3 6l9 7 9-7" /></svg>marktolvane@postbox.example</li>
        <li><svg viewBox="0 0 24 24"><circle cx="12" cy="12" r="10"/></svg>www.Marktolvane.example</li>
      </ul>
    </div>
    <div class="social"><span class="social-dot"></span>@MarkTolvanePlays</div>
  </section>

  <section class="card card-back">
    <div class="agency">
      <span class="agency-dot"></span>
      <div>
        <div class="agency-name">Kirwood</div>
        <div class="agency-sub">Talent Agency</div>
      </div>
    </div>
    <div class="pronoun-band"><p class="pronouns">He, Him, His</p></div>
  </section>
</body>
</html>
```